One pager digital ad-Corporate travel Manager

I need a design that is smooth, and business like. I don’t like basic generic designs that I can make my self. I’m looking for a sharp clean ad that clearly was made by a great designer. I need some bullet points in and the add to be clean. Here is a list of some content from our content writers. You can arrange and play with the words a bit.

*Budget*- having a travel management service will ensure that your company sticks to a budget which will help PROTECT your bottom line. Travel expenses often CAN BE COSTLY and having a SAVVY corporate travel manager handle YOUR TRAVEL ARRANGEMENTS will make sure that the travel expenses are kept under control.
*Efficiency- time *is money. Have your staff focus on their core business and have the corporate travel manager handle all the logistics for their travel including airfare, hotel cars and events TO MAXIMIZE EFFICIENCY AND KEEP YOUR STAFF FOCUSED ON YOUR CORE BUSINESS

*unforeseen circumstances* – the corporate travel manager handleS any cancellations, missed flights, canceled flights. Quick rebooking, and repositioning, and dealing with getting credits and reimbursement is extremely difficult and time-consuming. The corporate travel manager handles all of that SO YOU CAN CONTINUE ON SCHEDULE WITHOUT SPENDING HOURS REBOOKING AND GETTING CREDIT

Efficient and organized business travel management-help reduce travel expenses, streamline expense reports, optimize booking processes, and make managing the corporate travel experience way easier for all stakeholders involved.

Travel Support

Report on travel spend: In order to optimize their budgets, businesses need to know which departments are spending what on travel. Agencies can report on spend for all stakeholders by team, department, or project, and help you accurately track all your travel expenses.

Maintain compliance: Every company has some sort of rules that make up their travel policy. An agency can enforce these guidelines when booking.

Velnor Trips is a global leader in business travel management services. We drive savings, efficiency and safety to businesses and their travelers all around the world.

If you are looking for a tailored travel management solution, delivering customer service excellence, and a demonstrable return on investment, then you’ve come to the right place

Corporate travel policy compliance
Travel management reports
Meetings and event management
Travel program management
Dedicated travel counselor teams

By listening to your needs and focusing on your goals we can help your company design a global corporate travel service program that controls costs, improves traveler satisfaction and fits your corporate culture.

Our qualified business travel agents and cutting-edge technology deliver solutions that provide the best travel arrangements and travel policy adherence in the business. From CEO to support staff, our services can help make corporate travel a more efficient and enjoyable experience for everyone involved.

With so much involved in travel – from booking and expenses to meetings and strategy – you need the backing of a proven leader…
Velnor Trips, We’re your corporate travel partner to help you manage it all.

```html
<!DOCTYPE html>
<html lang="en">
<head>
<meta charset="utf-8">
<title>Velnor Trips – Corporate Travel Flyer</title>
<link href="https://fonts.googleapis.com/css2?family=Poppins:wght@300;400;500;600;700;800&display=swap" rel="stylesheet">
<style>
  :root{
    --navy:#0b1a33;
    --navy-deep:#081428;
    --cyan:#1fc9e8;
    --cyan-light:#3fd6ef;
    --cyan-panel:#22c3e3;
    --blue-band:#0b8fc6;
    --white:#ffffff;
    --charcoal:#1f2328;
    --grey-dot:#7b8698;
  }
  *{margin:0;padding:0;box-sizing:border-box}
  html,body{width:772px;height:1200px;overflow:hidden;background:var(--navy)}
  body{font-family:'Poppins',sans-serif;color:var(--white)}
  .flyer{position:relative;width:772px;height:1200px;overflow:hidden}

  /* ---------- left column ---------- */
  .intro{position:absolute;left:0;top:0;width:387px;height:1200px;background:var(--navy)}
  .brand{position:absolute;top:96px;left:0;width:320px;text-align:center;display:flex;justify-content:center;align-items:center;gap:8px}
  .brand-dot{width:8px;height:8px;border-radius:50%;background:var(--white)}
  .brand-name{font-weight:400;font-size:13px;letter-spacing:2.5px;color:var(--white)}

  .title{position:absolute;left:50px;top:150px;line-height:.88}
  .title-top{display:block;font-weight:800;font-size:64px;letter-spacing:-1px;color:var(--white)}
  .title-bottom{display:block;font-weight:300;font-size:64px;color:var(--cyan)}

  .lead{position:absolute;left:51px;top:318px;width:310px}
  .lead-head{font-weight:700;font-size:17px;line-height:21px}
  .lead-sub{margin-top:7px;font-size:10.5px;line-height:13px;color:var(--cyan)}

  .dots{position:absolute;left:51px;top:442px;display:flex;gap:3px}
  .dots span{width:5px;height:5px;border-radius:50%;background:var(--white)}
  .dots span:nth-child(3){background:#b9c2d0}
  .dots span:nth-child(4){background:var(--grey-dot)}

  .benefits{position:absolute;left:51px;top:462px;width:300px}
  .benefit{margin-bottom:13px}
  .benefit h3{font-weight:700;font-size:18px;line-height:22px;color:var(--cyan);margin-bottom:3px}
  .benefit p,.summary{font-size:10.3px;line-height:14.4px;color:var(--white)}
  .benefit strong{font-weight:700}
  .summary{margin-top:12px}

  .services{position:absolute;left:58px;top:974px;width:300px;height:164px;border:1.3px solid var(--cyan);border-radius:22px 22px 22px 22px;list-style:none;padding:14px 0 0 0}
  .services li{position:relative;padding-left:22px;margin-left:-8px;font-weight:500;font-size:14.2px;line-height:27.5px;color:var(--white);background:var(--navy);width:fit-content;padding-right:6px}
  .services svg{position:absolute;left:2px;top:8px;width:13px;height:13px}

  /* ---------- right column ---------- */
  .visual{position:absolute;left:387px;top:0;width:385px;height:1200px;background:linear-gradient(180deg,#2a2f35 0%,#1c1f24 70%,#141619 100%)}
  .window-view{position:absolute;left:0;top:0;width:340px;height:930px;border-radius:0 0 60px 0;
    background:linear-gradient(180deg,#6f8fae 0%,#c7d3de 18%,#e6ecf1 30%,#8e9aa4 45%,#5b646d 55%,#4a5561 64%);}
  .window-frame{position:absolute;right:0;top:0;width:60px;height:960px;background:linear-gradient(90deg,#3b3f45,#5c6168 45%,#2a2d31);border-radius:0 0 0 40px}

  .support{position:absolute;left:0;top:379px;width:340px;height:452px;border-radius:0 14px 0 0;
    background:linear-gradient(180deg,var(--cyan-light) 0%,var(--cyan-panel) 55%,#18b4d9 100%)}
  .support h2{position:absolute;left:30px;top:20px;font-weight:700;font-size:21.5px;letter-spacing:.2px;color:var(--navy)}
  .support-item{position:absolute;left:30px;width:290px}
  .support-item h4{font-weight:600;font-size:10.3px;line-height:14px;color:var(--navy)}
  .support-item p{font-size:10.3px;line-height:14.5px;color:var(--navy)}
  .support-item::after{content:"";position:absolute;left:0;right:-10px;bottom:-14px;height:1px;background:rgba(255,255,255,.35)}
  .support-item:last-of-type::after{display:none}

  .mission{position:absolute;left:0;top:831px;width:340px;height:100px;border-radius:0 0 18px 0;background:linear-gradient(180deg,#1aa2d4 0%,var(--blue-band) 100%)}
  .mission p{position:absolute;left:30px;top:15px;width:290px;font-weight:700;font-size:11.5px;line-height:14.5px;color:var(--white)}

  .tailored{position:absolute;left:30px;top:966px;font-weight:600;font-size:12.4px;color:var(--white);white-space:nowrap}
  .features{position:absolute;left:10px;top:992px;width:350px;display:flex;justify-content:space-between}
  .feature{width:112px;text-align:center;position:relative}
  .feature + .feature::before{content:"";position:absolute;left:-6px;top:0;height:90px;border-left:1px dashed #8a9099}
  .feature-icon{width:47px;height:47px;margin:0 auto;background:var(--cyan);border-radius:4px;display:flex;align-items:center;justify-content:center}
  .feature-icon svg{width:30px;height:30px}
  .feature span{display:block;margin-top:8px;font-weight:500;font-size:9.2px;line-height:10.6px;color:var(--white)}
  .web{position:absolute;left:0;top:1118px;width:385px;text-align:center;font-weight:500;font-size:19px;letter-spacing:5px;color:var(--white)}
  .web em{font-style:normal;color:var(--cyan)}
</style>
</head>
<body>
<main class="flyer">

  <section class="intro">
    <div class="brand"><span class="brand-dot"></span><span class="brand-name">VELNOR TRIPS</span></div>

    <h1 class="title"><span class="title-top">VELNOR</span><span class="title-bottom">TRIPS</span></h1>

    <div class="lead">
      <p class="lead-head">We’re your corporate travel partner to help you manage it all.</p>
      <p class="lead-sub">With so much involved in travel – from booking and expenses to meetings and strategy – you need the backing of a proven leader</p>
    </div>

    <div class="dots"><span></span><span></span><span></span><span></span></div>

    <div class="benefits">
      <article class="benefit">
        <h3>BUDGET</h3>
        <p>having a travel management service will ensure that your company sticks to a budget which will help PROTECT your bottom line. Travel expenses often CAN BE COSTLY and having a SAVVY corporate travel manager handle YOUR TRAVEL ARRANGEMENTS will make sure that the travel ex-penses are kept under control.</p>
      </article>
      <article class="benefit">
        <h3>EFFICIENCY</h3>
        <p>time is money. Have your staff focus on their core business and have the corporate travel manager handle all the logistics for their travel including airfare, hotel cars and events TO MAXIMIZE EFFICIENCY AND KEEP YOUR STAFF FOCUSED ON YOUR CORE BUSINESS</p>
      </article>
      <article class="benefit">
        <h3>UNFORESEEN CIRCUMSTANCES</h3>
        <p>the corporate travel manager handleS any cancellations, missed flights, canceled flights. Quick rebooking, and repositioning, and dealing with getting credits and reimbursement is extremely difficult and time-consuming. The corporate travel manager handles all of that SO YOU CAN CONTINUE ON SCHEDULE WITHOUT SPENDING HOURS <strong>REBOOKING AND GETTING CREDIT</strong></p>
        <p class="summary">Efficient and organized business travel management-help reduce travel expenses, streamline expense reports, optimize booking processes, and make managing the corporate travel experience way easier for all stakeholders involved.</p>
      </article>
    </div>

    <ul class="services">
      <li><svg viewBox="0 0 14 14"><rect x="1" y="2" width="11" height="11" rx="1.5" fill="none" stroke="#1fc9e8" stroke-width="1.6"/><path d="M3.5 7.5l2.5 2.5 6.5-8" fill="none" stroke="#1fc9e8" stroke-width="1.8"/></svg>Corporate travel policy compliance</li>
      <li><svg viewBox="0 0 14 14"><rect x="1" y="2" width="11" height="11" rx="1.5" fill="none" stroke="#1fc9e8" stroke-width="1.6"/><path d="M3.5 7.5l2.5 2.5 6.5-8" fill="none" stroke="#1fc9e8" stroke-width="1.8"/></svg>Travel management reports</li>
      <li><svg viewBox="0 0 14 14"><rect x="1" y="2" width="11" height="11" rx="1.5" fill="none" stroke="#1fc9e8" stroke-width="1.6"/><path d="M3.5 7.5l2.5 2.5 6.5-8" fill="none" stroke="#1fc9e8" stroke-width="1.8"/></svg>Meetings and event management</li>
      <li><svg viewBox="0 0 14 14"><rect x="1" y="2" width="11" height="11" rx="1.5" fill="none" stroke="#1fc9e8" stroke-width="1.6"/><path d="M3.5 7.5l2.5 2.5 6.5-8" fill="none" stroke="#1fc9e8" stroke-width="1.8"/></svg>Travel program management</li>
      <li><svg viewBox="0 0 14 14"><rect x="1" y="2" width="11" height="11" rx="1.5" fill="none" stroke="#1fc9e8" stroke-width="1.6"/><path d="M3.5 7.5l2.5 2.5 6.5-8" fill="none" stroke="#1fc9e8" stroke-width="1.8"/></svg>Dedicated travel counselor teams</li>
    </ul>
  </section>

  <section class="visual">
    <div class="window-view" role="img" aria-label="View through an airplane window of clouds over rugged mountain peaks"></div>
    <div class="window-frame" role="img" aria-label="Airplane window frame"></div>

    <div class="support">
      <h2>TRAVEL SUPPORT</h2>
      <div class="support-item" style="top:68px">
        <h4>REPORT ON TRAVEL SPEND</h4>
        <p>In order to optimize their budgets, businesses need to know which departments are spending what on travel. Agencies can report on spend for all stakeholders by team, department, or project, and help you accurately track all your travel expenses.</p>
      </div>
      <div class="support-item" style="top:192px">
        <h4>REPORT ON TRAVEL SPEND</h4>
        <p>In order to optimize their budgets, businesses need to know which departments are spending what on travel. Agencies can report on spend for all stakeholders by team, department, or project, and help you accurately track all your travel expenses.</p>
      </div>
      <div class="support-item" style="top:318px">
        <h4>REPORT ON TRAVEL SPEND</h4>
        <p>In order to optimize their budgets, businesses need to know which departments are spending what on travel. Agencies can report on spend for all stakeholders by team, department, or project, and help you accurately track all your travel expenses.</p>
      </div>
    </div>

    <div class="mission">
      <p>Velnor Trips is a global leader in business travel management services. We drive savings, efficiency and safety to businesses and their travelers all around the world.</p>
    </div>

    <p class="tailored">IF YOU ARE LOOKING FOR A TAILORED TRAVEL</p>

    <div class="features">
      <div class="feature">
        <div class="feature-icon"><svg viewBox="0 0 30 30"><circle cx="12" cy="8" r="5" fill="#0b1a33"/><path d="M3 24c0-6 4-9 9-9s8 2 9 5v4z" fill="#0b1a33"/><circle cx="22" cy="22" r="4" fill="none" stroke="#0b1a33" stroke-width="2.4" stroke-dasharray="2 1.2"/><circle cx="22" cy="22" r="1.3" fill="#0b1a33"/></svg></div>
        <span>Managment<br>solution</span>
      </div>
      <div class="feature">
        <div class="feature-icon"><svg viewBox="0 0 30 30"><circle cx="15" cy="6" r="3.5" fill="#0b1a33"/><path d="M10 16c0-4 2-6 5-6s5 2 5 6z" fill="#0b1a33"/><path d="M3 17l5 0 5 4h6a1.5 1.5 0 010 3h-5M8 26h10l9-7a1.7 1.7 0 00-2.4-2.4L19 20" fill="none" stroke="#0b1a33" stroke-width="2" stroke-linejoin="round"/></svg></div>
        <span>Delivering<br>customer service<br>excellence</span>
      </div>
      <div class="feature">
        <div class="feature-icon"><svg viewBox="0 0 30 30"><circle cx="16" cy="8" r="6" fill="none" stroke="#0b1a33" stroke-width="2"/><text x="16" y="11.5" text-anchor="middle" font-family="Poppins,sans-serif" font-weight="700" font-size="9" fill="#0b1a33">$</text><path d="M3 19l5 0 5 3h5a1.5 1.5 0 010 3h-4M8 27h10l9-7a1.7 1.7 0 00-2.4-2.4L19 21" fill="none" stroke="#0b1a33" stroke-width="2" stroke-linejoin="round"/></svg></div>
        <span>Demonstrable<br>return on<br>investment</span>
      </div>
    </div>

    <p class="web">www.<em>velnortrips</em>.com</p>
  </section>

</main>
</body>
</html>
```